Business Cards - Brightpath Horizon

need to design unique business card for my mortgage business. I need to design credit card style business card for my business or any unique idea that you might have

Target Market(s)

Home Loan customers

Industry/Entity Type

Mortgage Brokerage

Contact Information for Business Card

please design credit card style or very unique style business card

Colors

Designer to choose colors to be used in the design.

Requirements
Must have
• Name
• position
• Phone number
• fax number
• email address
• website address
• social media address
• All above fields will be provided once design in finalised

```html
<!DOCTYPE html>
<html lang="en">
<head>
<meta charset="utf-8">
<title>Brightpath Horizon – Business Card</title>
<link rel="stylesheet" href="https://fonts.googleapis.com/css2?family=Roboto:wght@400;500;700&display=swap">
<style>
  :root {
    --backdrop: #232323;
    --paper: #f1f1f1;
    --brand-blue: #0630c9;
    --sky-blue: #22a6ff;
    --brand-orange: #ff8c14;
    --white: #ffffff;
  }
  * { margin: 0; padding: 0; box-sizing: border-box; }
  html, body { width: 1200px; height: 960px; overflow: hidden; }
  body {
    background: var(--backdrop);
    font-family: "Roboto", Arial, sans-serif;
    position: relative;
  }
  .card {
    position: absolute;
    width: 600px;
    height: 343px;
    overflow: hidden;
  }
  .card-front { left: 314px; top: 113px; background: var(--paper); }
  .card-back { left: 311px; top: 472px; background: var(--brand-orange); }

  .front-divider { position: absolute; left: 0; top: 0; }

  .brand-block {
    position: absolute;
    left: 0; top: 0;
    width: 340px; height: 343px;
    display: flex; flex-direction: column;
    align-items: center; justify-content: center;
  }
  .brand-name {
    font-weight: 700;
    font-size: 30px;
    letter-spacing: 1px;
    line-height: 1.05;
    text-align: center;
    text-transform: uppercase;
    display: flex; align-items: center; gap: 10px;
  }
  .brand-mark { width: 14px; height: 14px; flex: none; }
  .brand-tagline {
    margin-top: 10px;
    font-size: 15px;
    font-weight: 500;
  }
  .card-front .brand-name { color: var(--brand-blue); }
  .card-front .brand-mark { background: var(--brand-orange); }
  .card-front .brand-tagline { color: var(--brand-orange); }

  .contact-panel {
    position: absolute;
    left: 383px; top: 0;
    color: var(--white);
  }
  .person-name {
    position: absolute; top: 64px; left: 0;
    font-size: 20px; font-weight: 500;
    color: var(--sky-blue);
    white-space: nowrap;
  }
  .person-role {
    position: absolute; top: 91px; left: 0;
    font-size: 15px; font-weight: 500;
    white-space: nowrap;
  }
  .address {
    position: absolute; top: 154px; left: 0;
    font-size: 14px; line-height: 18px;
    font-style: normal;
    white-space: nowrap;
  }
  .contact-list {
    position: absolute; top: 200px; left: 0;
    list-style: none;
    font-size: 14px; line-height: 19.3px;
    white-space: nowrap;
  }
  .contact-list li { display: flex; align-items: center; gap: 8px; }
  .contact-list svg { width: 14px; height: 14px; fill: var(--sky-blue); flex: none; }

  .card-back .brand-block { width: 600px; height: 300px; top: 0; }
  .card-back .brand-name { color: var(--white); font-size: 34px; }
  .card-back .brand-mark { background: var(--white); }
  .card-back .brand-tagline { color: var(--white); font-size: 16px; }

  .social-row {
    position: absolute; left: 0; top: 290px;
    width: 600px;
    display: flex; align-items: center; justify-content: center; gap: 5px;
  }
  .social-rule { height: 1px; width: 160px; }
  .social-rule.left { background: linear-gradient(to right, rgba(255,255,255,0), var(--white)); margin-right: 8px; }
  .social-rule.right { background: linear-gradient(to left, rgba(255,255,255,0), var(--white)); margin-left: 8px; }
  .social-dot { width: 28px; height: 28px; border-radius: 50%; background: var(--white); }
</style>
</head>
<body>

<section class="card card-front" aria-label="Business card front">
  <svg class="front-divider" width="600" height="343" viewBox="0 0 600 343">
    <path d="M344 0 H600 V343 H344 V102 L362 82 L344 62 Z" fill="var(--brand-blue)"/>
    <path d="M341 0 V62 L359 82 L341 102 V343" fill="none" stroke="var(--brand-orange)" stroke-width="3"/>
    <rect x="334" y="77" width="10" height="10" fill="var(--brand-orange)"/>
  </svg>

  <div class="brand-block">
    <div class="brand-name"><span class="brand-mark"></span>Brightpath<br>Horizon</div>
    <div class="brand-tagline">Smart loans, Steady homes</div>
  </div>

  <div class="contact-panel">
    <div class="person-name">DANIEL REYES</div>
    <div class="person-role">CEO/FOUNDER</div>
    <address class="address">4120 Maple Ridge Road<br>Fairbanks, Alaska 99709</address>
    <ul class="contact-list">
      <li><svg viewBox="0 0 16 16"><path d="M3 1l3 3-1.5 2c1 2 2.5 3.5 4.5 4.5L11 9l3 3-2 3C6 14 2 10 1 3z"/></svg>555 213 4860</li>
      <li><svg viewBox="0 0 16 16"><rect x="4" y="1" width="8" height="4"/><rect x="1" y="6" width="14" height="6" rx="1"/><rect x="4" y="11" width="8" height="4"/></svg>555 213 4871</li>
      <li><svg viewBox="0 0 16 16"><path d="M1 4h14v9H1z M1 4l7 5 7-5" stroke="var(--brand-blue)" stroke-width="1"/></svg>mail@bphorizon.com</li>
      <li><svg viewBox="0 0 16 16"><circle cx="8" cy="8" r="7"/><path d="M1 8h14M8 1c-3 4-3 10 0 14M8 1c3 4 3 10 0 14" fill="none" stroke="var(--brand-blue)" stroke-width="1"/></svg>www.bphorizon.com</li>
    </ul>
  </div>
</section>

<section class="card card-back" aria-label="Business card back">
  <div class="brand-block">
    <div class="brand-name"><span class="brand-mark"></span>Brightpath<br>Horizon</div>
    <div class="brand-tagline">Smart loans, Steady homes</div>
  </div>
  <div class="social-row">
    <span class="social-rule left"></span>
    <span class="social-dot" role="img" aria-label="Social network link"></span>
    <span class="social-dot" role="img" aria-label="Social network link"></span>
    <span class="social-dot" role="img" aria-label="Social network link"></span>
    <span class="social-dot" role="img" aria-label="Social network link"></span>
    <span class="social-rule right"></span>
  </div>
</section>

</body>
</html>
```